Double sided 8.5x11 Flyer

The attached text should be in the flyer. this is an election flyer for a board of director role for automotive racing industry. Try to make it exciting!

```html
<!DOCTYPE html>
<html lang="en">
<head>
<meta charset="utf-8">
<title>Daniel Kessler for ASPA Board – Election Flyer</title>
<link href="https://fonts.googleapis.com/css2?family=Montserrat:wght@400;500;600;700;800&display=swap" rel="stylesheet">
<style>
:root{
  --teal:#0d3a3d;
  --teal-band:#124447;
  --green:#3b7f5b;
  --grey:#e7e7e7;
  --grey-row:#dedede;
  --grey-dark:#595959;
  --ink:#333;
  --bg:#f1f1f1;
  --red:#d9232d;
}
*{margin:0;padding:0;box-sizing:border-box}
html,body{width:783px;height:1200px;overflow:hidden;background:var(--bg);font-family:'Montserrat',sans-serif;color:var(--ink)}
.canvas{position:relative;width:783px;height:1200px}
.sheet{position:absolute;background:#fff;box-shadow:0 2px 8px rgba(0,0,0,.18);overflow:hidden}
.front{width:348px;height:447px}
.front--hero{left:217px;top:80px}
.front--pair{left:37px;top:681px;transform:scale(.954);transform-origin:0 0}
.abs{position:absolute}
.txt{font-size:5.3px;line-height:6.1px}
.spiral{left:0;top:0;width:165px;height:30px}
.side-panel{left:0;top:0;width:165px;height:447px}
.side-text{color:#e8f0ef;left:22px;width:131px;font-size:5.5px;line-height:6.1px}
.side-text b{font-weight:700;color:#fff}
.stop-head{left:61px;top:43px;width:94px;color:#fff;font-size:8px;line-height:9.4px;font-weight:500}
.photo{left:170px;top:0;width:178px;height:113px;background:radial-gradient(ellipse at 55% 45%,#fbfbfb 0%,#d8d8d8 70%,#c9c9c9 100%)}
.name-band{left:170px;top:113px;width:178px;height:27px;background:var(--grey-dark);color:#fff;text-align:center}
.name-band h1{font-size:11.5px;line-height:13px;font-weight:800;letter-spacing:.3px;margin-top:4px}
.name-band p{font-size:5.3px;line-height:6px}
.tag{height:8px;background:var(--teal);color:#fff;font-size:5.2px;line-height:6px;font-weight:700;padding:1px 0 0 17px;clip-path:polygon(0 0,100% 0,92% 100%,0 100%)}
.icon-dot{width:14px;height:14px;border-radius:50%;background:#cfcfcf;border:1.5px solid #fff;box-shadow:0 0 0 .6px #aaa}
.passions-bar{left:173px;width:175px;height:20px;background:var(--teal);color:#fff;font-size:7px;line-height:8px;font-weight:700;padding:6px 0 0 20px}
.list{left:180px;font-size:5px;font-weight:600;color:#333;list-style:none}
.list li{position:relative;padding-left:10px;margin-bottom:3.1px;line-height:5.6px}
.list li::before{content:"";position:absolute;left:0;top:0;width:6px;height:6px;border-radius:50%;background:var(--green)}
.list li::after{content:"";position:absolute;left:1.6px;top:1.3px;width:2.2px;height:1.2px;border-left:1px solid #fff;border-bottom:1px solid #fff;transform:rotate(-45deg)}
.web-box{background:var(--teal);color:#fff;padding:2px 0 0 6px}
.web-box small{display:block;font-size:4px;line-height:5px}
.web-box strong{display:block;font-size:6.2px;line-height:8px;font-weight:700}
.call{color:#fff;font-weight:700;font-size:10px;line-height:12px;letter-spacing:.4px;white-space:nowrap}
.call span{font-size:7.5px}
.back{left:402px;top:680px;width:335px;height:431px}
.banner{background:var(--teal);color:#fff;font-weight:700;text-align:center;border-radius:10px 10px 0 0;line-height:10px}
.role-table{left:15px;top:27px;width:303px;height:187px;border:1px solid #cfcfcf;border-radius:6px;overflow:hidden;padding-top:12px}
.role-row{display:flex}
.role-row--shade{background:var(--grey-row)}
.role-cell{width:50%;padding:4px 9px 0;font-size:4.6px;line-height:5.6px}
.role-cell:first-child{border-right:1px solid #cfcfcf}
.role-cell b{display:block;font-weight:700;font-size:4.7px}
.factory{left:16px;top:220px;width:302px;height:82px;border-radius:5px;background:linear-gradient(180deg,#8d969c 0%,#c7c9c6 40%,#7a6d60 100%)}
.quote-table{top:316px;width:145px;border:1px solid #cfcfcf;border-radius:6px;overflow:hidden;font-size:4.1px}
.quote-head{display:flex;background:var(--green);color:#fff;font-weight:700;font-size:5px;height:14px;align-items:center}
.quote-row{display:flex;height:12.8px;align-items:center;border-top:1px solid #ddd}
.quote-row:nth-child(odd){background:#f2f2f2}
.q-name{width:36px;padding-left:6px}
.q-text{flex:1;padding-left:4px}
</style>
</head>
<body>
<div class="canvas">

<section class="sheet front front--hero">
  <svg class="abs side-panel" viewBox="0 0 165 447" aria-hidden="true">
    <rect x="0" y="30" width="165" height="362" fill="#0d3a3d"/>
    <rect x="0" y="88" width="165" height="22" fill="#124447"/>
    <rect x="0" y="110" width="165" height="3" fill="#0a3134"/>
    <rect x="0" y="187" width="165" height="3" fill="#0a3134"/>
    <rect x="0" y="237" width="165" height="3" fill="#0a3134"/>
    <path d="M165 240 L165 392 L104 392 C130 370 150 330 165 240 Z" fill="#fff"/>
    <path d="M104 392 C125 378 140 360 150 340 C142 360 136 378 138 392 Z" fill="#3b7f5b"/>
  </svg>
  <svg class="abs spiral" viewBox="0 0 165 30" aria-hidden="true">
    <rect width="165" height="30" fill="#fff"/>
    <rect x="0" y="22" width="165" height="8" fill="#0d3a3d"/>
    <g fill="none" stroke="#222" stroke-width="1.6">
      <path d="M5 24V6a2 2 0 0 1 4 0V24M11 24V6a2 2 0 0 1 4 0V24M19 24V6a2 2 0 0 1 4 0V24M25 24V6a2 2 0 0 1 4 0V24M33 24V6a2 2 0 0 1 4 0V24M39 24V6a2 2 0 0 1 4 0V24M47 24V6a2 2 0 0 1 4 0V24M53 24V6a2 2 0 0 1 4 0V24M61 24V6a2 2 0 0 1 4 0V24M67 24V6a2 2 0 0 1 4 0V24M75 24V6a2 2 0 0 1 4 0V24M81 24V6a2 2 0 0 1 4 0V24M89 24V6a2 2 0 0 1 4 0V24M95 24V6a2 2 0 0 1 4 0V24M103 24V6a2 2 0 0 1 4 0V24M109 24V6a2 2 0 0 1 4 0V24M117 24V6a2 2 0 0 1 4 0V24M123 24V6a2 2 0 0 1 4 0V24M131 24V6a2 2 0 0 1 4 0V24M137 24V6a2 2 0 0 1 4 0V24M145 24V6a2 2 0 0 1 4 0V24M151 24V6a2 2 0 0 1 4 0V24"/>
    </g>
  </svg>
  <svg class="abs" style="left:22px;top:45px" width="33" height="33" viewBox="0 0 33 33" aria-hidden="true">
    <polygon points="10,1 23,1 32,10 32,23 23,32 10,32 1,23 1,10" fill="#fff"/>
    <polygon points="10.6,2.5 22.4,2.5 30.5,10.6 30.5,22.4 22.4,30.5 10.6,30.5 2.5,22.4 2.5,10.6" fill="#d9232d"/>
    <text x="16.5" y="20" text-anchor="middle" font-family="Montserrat,sans-serif" font-weight="800" font-size="9" fill="#fff">STOP</text>
  </svg>
  <p class="abs stop-head">I need 30 seconds of your time. I promise it's important. Read Below...</p>
  <p class="abs side-text" style="top:93px;width:110px;font-size:5.6px;line-height:6.6px">New cars are not designed with modification in mind</p>
  <p class="abs side-text" style="top:117px">You are probably aware that some autonomous vehicle technology is showing up as features in cars today and will be mandated in a few years. This Technology is called ADAS, or Advanced Driver Assist Systems. What you may not know is that ADAS systems can malfunction when vehicles are modified. Not just performance and racing, this affects wheels and tires, body modifications, paint (yes, increasing paint thickness on a bumper can cause these systems to read distances wrong), interior changes, and so much more.</p>
  <p class="abs side-text" style="top:196px;width:125px"><b>If we don't get in front of ADAS as an aftermarket industry, vehicle customization will impact driver safety and we can expect government regulation preventing modification</b></p>
  <p class="abs side-text" style="top:227px">And limiting our future of vehicle customization.</p>
  <p class="abs side-text" style="top:247px;width:125px">I can't stand to the side and watch this happen. I love performance cars, racing, vehicle modification, and customization. I managed RTC and several other startups, I modify my own cars and my daily driver has 1000 HP, I have a NDRA competition license, and I believe that for many ASPA members the opportunity to customize is a way of life.</p>
  <p class="abs side-text" style="top:303px;width:112px">I am running for ASPA director because I can drive change. I have made real change in the repair industry thru right to repair and Automaker relationships, and I have the experience, relationships, leadership, motivation, and drive to push the full force of ASPA towards this problem before it's too late. All I need to get started is your vote.</p>

  <div class="abs photo" role="img" aria-label="Portrait photo of candidate Daniel Kessler in a dark suit"></div>
  <div class="abs name-band"><h1>DANIEL KESSLER</h1><p>President - Northgate Diagnostics</p></div>

  <div class="abs icon-dot" style="left:172px;top:146px"></div>
  <div class="abs tag" style="left:181px;top:149px;width:70px">PROBLEM</div>
  <p class="abs txt" style="left:173px;top:162px;width:160px">ADAS systems often stop functioning when a vehicle is modified</p>
  <div class="abs icon-dot" style="left:172px;top:179px"></div>
  <div class="abs tag" style="left:181px;top:182px;width:70px">MY SOLUTION</div>
  <p class="abs txt" style="left:173px;top:195px;width:160px">My Solution is to activate the Full strength of ASPA and it's network to engage Automakers, Regulators, and Industry. Vehicles must be designed with modification in mind, and there must be a partnership and transparency with the aftermarket.</p>
  <div class="abs icon-dot" style="left:172px;top:230px"></div>
  <div class="abs tag" style="left:181px;top:233px;width:118px">LEADERSHIP AND EXPERIENCE</div>
  <p class="abs txt" style="left:173px;top:248px;width:160px">I bring my Leadership and Experience as President of Northgate Diagnostics, a technology business that helps technicians with complex vehicles repairs and ADAS calibration, previous General Manager of RTC, experience with right to repair regulations, Automaker and government relationships, Inventor on over 60 patents.</p>

  <div class="abs" style="left:165px;top:296px;width:183px;height:99px;background:var(--grey)"></div>
  <div class="abs passions-bar" style="top:300px">MY PASSIONS KEEP ME MOTIVATED</div>
  <svg class="abs" style="left:177px;top:302px" width="14" height="16" viewBox="0 0 14 16" aria-hidden="true"><g fill="none" stroke="#fff" stroke-width="1"><path d="M3 7v4a4 4 0 0 0 8 0V6M5 7V3M7 7V2M9 7V3"/><circle cx="7" cy="12" r="2"/></g></svg>
  <ul class="abs list" style="top:326px;width:160px">
    <li>Resto-mod projects at home (last was a '75 Trailmaster 4x4 powertrain swap)</li>
    <li>Fast Cars (1000 HP Daily Driver V-Sedan)</li>
    <li>NDRA Comp Licensed Driver</li>
    <li>Pilot, multi engine, instrument and Jet rated</li>
    <li>Hobbyist collector car broker</li>
    <li>Hobbyist airplane dealer</li>
    <li>Driving change in whatever I do</li>
  </ul>

  <div class="abs" style="left:0;top:392px;width:348px;height:55px;background:#fff"></div>
  <div class="abs" style="left:115px;top:396px;width:217px;height:18px;background:var(--grey)"></div>
  <div class="abs web-box" style="left:22px;top:396px;width:93px;height:18px"><small>More on these at my website</small><strong>www.KesslerASPA.com</strong></div>
  <p class="abs" style="left:122px;top:400px;width:205px;font-size:4.9px;line-height:5.8px;font-weight:500">To learn more details on the challenge, my vision for solving these problems, and my credentials and experience to make it happen.</p>
  <p class="abs" style="left:22px;top:422px;font-size:6.2px;line-height:8px;color:#222">You can also contact me directly at<br><b>daniel.kessler@northgatediag.com</b></p>
  <div class="abs" style="left:140px;top:419px;width:208px;height:28px;background:var(--green);clip-path:polygon(11% 0,100% 0,100% 100%,0 100%)"></div>
  <p class="abs call" style="left:163px;top:427px"><span>CALL US NOW: </span>(555) 014-2390</p>
</section>

<section class="sheet front front--pair">
  <svg class="abs side-panel" viewBox="0 0 165 447" aria-hidden="true">
    <rect x="0" y="30" width="165" height="362" fill="#0d3a3d"/>
    <rect x="0" y="88" width="165" height="22" fill="#124447"/>
    <rect x="0" y="110" width="165" height="3" fill="#0a3134"/>
    <rect x="0" y="187" width="165" height="3" fill="#0a3134"/>
    <rect x="0" y="237" width="165" height="3" fill="#0a3134"/>
    <path d="M165 240 L165 392 L104 392 C130 370 150 330 165 240 Z" fill="#fff"/>
    <path d="M104 392 C125 378 140 360 150 340 C142 360 136 378 138 392 Z" fill="#3b7f5b"/>
  </svg>
  <svg class="abs spiral" viewBox="0 0 165 30" aria-hidden="true">
    <rect width="165" height="30" fill="#fff"/>
    <rect x="0" y="22" width="165" height="8" fill="#0d3a3d"/>
    <g fill="none" stroke="#222" stroke-width="1.6">
      <path d="M5 24V6a2 2 0 0 1 4 0V24M11 24V6a2 2 0 0 1 4 0V24M19 24V6a2 2 0 0 1 4 0V24M25 24V6a2 2 0 0 1 4 0V24M33 24V6a2 2 0 0 1 4 0V24M39 24V6a2 2 0 0 1 4 0V24M47 24V6a2 2 0 0 1 4 0V24M53 24V6a2 2 0 0 1 4 0V24M61 24V6a2 2 0 0 1 4 0V24M67 24V6a2 2 0 0 1 4 0V24M75 24V6a2 2 0 0 1 4 0V24M81 24V6a2 2 0 0 1 4 0V24M89 24V6a2 2 0 0 1 4 0V24M95 24V6a2 2 0 0 1 4 0V24M103 24V6a2 2 0 0 1 4 0V24M109 24V6a2 2 0 0 1 4 0V24M117 24V6a2 2 0 0 1 4 0V24M123 24V6a2 2 0 0 1 4 0V24M131 24V6a2 2 0 0 1 4 0V24M137 24V6a2 2 0 0 1 4 0V24M145 24V6a2 2 0 0 1 4 0V24M151 24V6a2 2 0 0 1 4 0V24"/>
    </g>
  </svg>
  <svg class="abs" style="left:22px;top:45px" width="33" height="33" viewBox="0 0 33 33" aria-hidden="true">
    <polygon points="10,1 23,1 32,10 32,23 23,32 10,32 1,23 1,10" fill="#fff"/>
    <polygon points="10.6,2.5 22.4,2.5 30.5,10.6 30.5,22.4 22.4,30.5 10.6,30.5 2.5,22.4 2.5,10.6" fill="#d9232d"/>
    <text x="16.5" y="20" text-anchor="middle" font-family="Montserrat,sans-serif" font-weight="800" font-size="9" fill="#fff">STOP</text>
  </svg>
  <p class="abs stop-head">I need 30 seconds of your time. I promise it's important. Read Below...</p>
  <p class="abs side-text" style="top:93px;width:110px;font-size:5.6px;line-height:6.6px">New cars are not designed with modification in mind</p>
  <p class="abs side-text" style="top:117px">You are probably aware that some autonomous vehicle technology is showing up as features in cars today and will be mandated in a few years. This Technology is called ADAS, or Advanced Driver Assist Systems. What you may not know is that ADAS systems can malfunction when vehicles are modified. Not just performance and racing, this affects wheels and tires, body modifications, paint (yes, increasing paint thickness on a bumper can cause these systems to read distances wrong), interior changes, and so much more.</p>
  <p class="abs side-text" style="top:196px;width:125px"><b>If we don't get in front of ADAS as an aftermarket industry, vehicle customization will impact driver safety and we can expect government regulation preventing modification</b></p>
  <p class="abs side-text" style="top:227px">And limiting our future of vehicle customization.</p>
  <p class="abs side-text" style="top:247px;width:125px">I can't stand to the side and watch this happen. I love performance cars, racing, vehicle modification, and customization. I managed RTC and several other startups, I modify my own cars and my daily driver has 1000 HP, I have a NDRA competition license, and I believe that for many ASPA members the opportunity to customize is a way of life.</p>
  <p class="abs side-text" style="top:303px;width:112px">I am running for ASPA director because I can drive change. I have made real change in the repair industry thru right to repair and Automaker relationships, and I have the experience, relationships, leadership, motivation, and drive to push the full force of ASPA towards this problem before it's too late. All I need to get started is your vote.</p>

  <div class="abs photo" role="img" aria-label="Portrait photo of candidate Daniel Kessler in a dark suit"></div>
  <div class="abs name-band"><h1>DANIEL KESSLER</h1><p>President - Northgate Diagnostics</p></div>

  <div class="abs icon-dot" style="left:172px;top:146px"></div>
  <div class="abs tag" style="left:181px;top:149px;width:70px">PROBLEM</div>
  <p class="abs txt" style="left:173px;top:162px;width:160px">ADAS systems often stop functioning when a vehicle is modified</p>
  <div class="abs icon-dot" style="left:172px;top:179px"></div>
  <div class="abs tag" style="left:181px;top:182px;width:70px">MY SOLUTION</div>
  <p class="abs txt" style="left:173px;top:195px;width:160px">My Solution is to activate the Full strength of ASPA and it's network to engage Automakers, Regulators, and Industry. Vehicles must be designed with modification in mind, and there must be a partnership and transparency with the aftermarket.</p>
  <div class="abs icon-dot" style="left:172px;top:230px"></div>
  <div class="abs tag" style="left:181px;top:233px;width:118px">LEADERSHIP AND EXPERIENCE</div>
  <p class="abs txt" style="left:173px;top:248px;width:160px">I bring my Leadership and Experience as President of Northgate Diagnostics, a technology business that helps technicians with complex vehicles repairs and ADAS calibration, previous General Manager of RTC, experience with right to repair regulations, Automaker and government relationships, Inventor on over 60 patents.</p>

  <div class="abs" style="left:165px;top:296px;width:183px;height:99px;background:var(--grey)"></div>
  <div class="abs passions-bar" style="top:300px">MY PASSIONS KEEP ME MOTIVATED</div>
  <svg class="abs" style="left:177px;top:302px" width="14" height="16" viewBox="0 0 14 16" aria-hidden="true"><g fill="none" stroke="#fff" stroke-width="1"><path d="M3 7v4a4 4 0 0 0 8 0V6M5 7V3M7 7V2M9 7V3"/><circle cx="7" cy="12" r="2"/></g></svg>
  <ul class="abs list" style="top:326px;width:160px">
    <li>Resto-mod projects at home (last was a '75 Trailmaster 4x4 powertrain swap)</li>
    <li>Fast Cars (1000 HP Daily Driver V-Sedan)</li>
    <li>NDRA Comp Licensed Driver</li>
    <li>Pilot, multi engine, instrument and Jet rated</li>
    <li>Hobbyist collector car broker</li>
    <li>Hobbyist airplane dealer</li>
    <li>Driving change in whatever I do</li>
  </ul>

  <div class="abs" style="left:0;top:392px;width:348px;height:55px;background:#fff"></div>
  <div class="abs" style="left:115px;top:396px;width:217px;height:18px;background:var(--grey)"></div>
  <div class="abs web-box" style="left:22px;top:396px;width:93px;height:18px"><small>More on these at my website</small><strong>www.KesslerASPA.com</strong></div>
  <p class="abs" style="left:122px;top:400px;width:205px;font-size:4.9px;line-height:5.8px;font-weight:500">To learn more details on the challenge, my vision for solving these problems, and my credentials and experience to make it happen.</p>
  <p class="abs" style="left:22px;top:422px;font-size:6.2px;line-height:8px;color:#222">You can also contact me directly at<br><b>daniel.kessler@northgatediag.com</b></p>
  <div class="abs" style="left:140px;top:419px;width:208px;height:28px;background:var(--green);clip-path:polygon(11% 0,100% 0,100% 100%,0 100%)"></div>
  <p class="abs call" style="left:163px;top:427px"><span>CALL US NOW: </span>(555) 014-2390</p>
</section>

<section class="sheet back">
  <div class="abs role-table">
    <div class="role-row" style="height:31px">
      <div class="role-cell"><b>Standardized Vehicle Diagnostics</b>As a co-founder of Halden Technologies, our company helped realize the industry achieve standardized dealer diagnostics</div>
      <div class="role-cell"><b>Access to factory vehicle diagnostics for everyone</b>I personally played an active role in Right to Repair</div>
    </div>
    <div class="role-row role-row--shade" style="height:33px">
      <div class="role-cell"><b>Modernization of Performance Calibration</b>I became General Manager of RTC, during its startup phase, and helped that company bring flash tuning and DIY vehicle calibration mainstream</div>
      <div class="role-cell"><b>Keeping Overreaching patents from affecting our industry</b>By litigating against the biggest companies and winning, I helped re-shaping patent law to protect overreach</div>
    </div>
    <div class="role-row" style="height:37px">
      <div class="role-cell"><b>Configurable Gauge Displays</b>I was a co-inventor of the first user configurable LCD Gauge Display, patented and delivered at ASPA 2007 called DashView. This technology has spread throughout the industry.</div>
      <div class="role-cell"><b>Helping Mechanics support multi-brands of vehicles</b>I led the acquisition of Autoscan and Clearpoint, which day, under the Northgate Diagnostics Umbrella deliver remote diagnostic assistance using dealer trained techs</div>
    </div>
    <div class="role-row role-row--shade" style="height:34px">
      <div class="role-cell"><b>Remote Programming</b>I was co-inventor of remote programming under Northgate Diagnostics (Known as RSU), allowing remote software updates of vehicles</div>
      <div class="role-cell"><b>Helping Collision repairers keep cars safe</b>The company I run (Northgate Diagnostics) helps scan vehicles after collisions and complete ADAS Calibrations that ensures vehicles are safe when they return on the road</div>
    </div>
    <div class="role-row" style="height:40px">
      <div class="role-cell"><b>Building Business</b>I've helped build and recover automotive businesses, from startup to now nearly 400 employees across 7 offices and 3 continents that touch over a million vehicles per year</div>
      <div class="role-cell"><b>Porting Superchargers</b>Thru the first company I founded, Arvex, I brought supercharger porting to the mainstream for the Vexa Striker and Bolt</div>
    </div>
  </div>
  <div class="abs banner" style="left:48px;top:15px;width:239px;height:24px;font-size:8.6px;padding-top:7px">THE INDUSTRY I'VE PLAYED A KEY ROLE IN</div>

  <div class="abs factory" role="img" aria-label="Photo of robotic arms assembling a car body on a factory line"></div>
  <div class="abs banner" style="left:78px;top:292px;width:177px;height:20px;font-size:8.2px;padding-top:6px">ENDORSEMENTS FROM INDUSTRY</div>

  <div class="abs quote-table" style="left:15px">
    <div class="quote-head"><span class="q-name" style="padding-left:9px">NAME</span><span class="q-text" style="text-align:center">QUOTE</span></div>
    <div class="quote-row"><span class="q-name">Name Title</span><span class="q-text">One sentence quote here about Daniel Kessler</span></div>
    <div class="quote-row"><span class="q-name">Name Title</span><span class="q-text">One sentence quote here about Daniel Kessler</span></div>
    <div class="quote-row"><span class="q-name">Name Title</span><span class="q-text">One sentence quote here about Daniel Kessler</span></div>
    <div class="quote-row"><span class="q-name">Name Title</span><span class="q-text">One sentence quote here about Daniel Kessler</span></div>
    <div class="quote-row"><span class="q-name">Name Title</span><span class="q-text">One sentence quote here about Daniel Kessler</span></div>
  </div>
  <div class="abs quote-table" style="left:173px">
    <div class="quote-head"><span class="q-name" style="padding-left:9px">NAME</span><span class="q-text" style="text-align:center">QUOTE</span></div>
    <div class="quote-row"><span class="q-name">Name Title</span><span class="q-text">One sentence quote here about Daniel Kessler</span></div>
    <div class="quote-row"><span class="q-name">Name Title</span><span class="q-text">One sentence quote here about Daniel Kessler</span></div>
    <div class="quote-row"><span class="q-name">Name Title</span><span class="q-text">One sentence quote here about Daniel Kessler</span></div>
    <div class="quote-row"><span class="q-name">Name Title</span><span class="q-text">One sentence quote here about Daniel Kessler</span></div>
    <div class="quote-row"><span class="q-name">Name Title</span><span class="q-text">One sentence quote here about Daniel Kessler</span></div>
  </div>

  <div class="abs" style="left:0;top:404px;width:206px;height:27px;background:var(--green);clip-path:polygon(0 0,94% 0,100% 100%,0 100%)"></div>
  <p class="abs call" style="left:15px;top:412px"><span>CALL US NOW: </span>(555) 014-2390</p>
  <p class="abs" style="left:208px;top:408px;font-size:4.6px;line-height:5px;font-weight:600">More on these at my website</p>
  <p class="abs" style="left:208px;top:415px;font-size:8.6px;line-height:10px;font-weight:700;color:var(--teal)">www.KesslerASPA.com</p>
</section>

</div>
</body>
</html>
```